Marwick Law Letterhead

We need a new letterhead design for a Law Firm. The address for the law firm is 1475 Calloway Street, Suite 210, Houston, Texas 77041. Phone Number: 832-361-9027; Fax Number: 832-614-7359. The logo is uploaded to the project.

```html
<!DOCTYPE html>
<html lang="en">
<head>
<meta charset="utf-8">
<title>Marwick Law Letterhead</title>
<link href="https://fonts.googleapis.com/css2?family=Montserrat:wght@400;600&display=swap" rel="stylesheet">
<style>
  :root {
    --backdrop: #e4e4e4;
    --paper: #ffffff;
    --navy: #1b3261;
    --red: #d5141f;
    --red-deep: #7a0410;
    --ink: #222222;
  }
  * { margin: 0; padding: 0; box-sizing: border-box; }
  html, body {
    width: 1200px; height: 960px; overflow: hidden;
    background: var(--backdrop);
    font-family: "Montserrat", Arial, sans-serif;
  }
  .letterhead {
    position: absolute; left: 260px; top: 40px;
    width: 680px; height: 880px;
    background: var(--paper);
    box-shadow: 0 6px 24px rgba(0,0,0,0.12);
    overflow: hidden;
  }
  .brand {
    position: absolute; left: 50px; top: 62px;
    display: flex; align-items: center; gap: 10px;
  }
  .brand-square { width: 22px; height: 22px; background: var(--navy); }
  .brand-name {
    font-weight: 600; font-size: 22px; color: var(--navy);
    letter-spacing: 0.5px;
  }
  .contact {
    position: absolute; left: 462px; top: 46px;
    font-size: 10.5px; line-height: 14px; color: var(--ink);
  }
  .contact-line { display: flex; align-items: center; gap: 6px; }
  .contact-line svg { width: 10px; height: 10px; fill: var(--red); flex: none; }
  .contact-divider {
    position: absolute; left: 450px; top: 56px;
    width: 1px; height: 58px; background: var(--red);
  }
  .header-rule {
    position: absolute; left: 120px; top: 122px;
    width: 500px; height: 1.5px; background: var(--red);
  }
  .corner-bands { position: absolute; left: 0; bottom: 0; width: 680px; height: 60px; }
</style>
</head>
<body>
  <div class="letterhead">
    <div class="brand">
      <span class="brand-square"></span>
      <span class="brand-name">Marwick Law</span>
    </div>

    <div class="contact-divider"></div>
    <div class="contact">
      <div>1475 Calloway Street,</div>
      <div>Suite 210, Houston,</div>
      <div>Texas 77041</div>
      <div class="contact-line">
        <svg viewBox="0 0 24 24" aria-hidden="true"><path d="M6.6 10.8a15.1 15.1 0 0 0 6.6 6.6l2.2-2.2a1 1 0 0 1 1-.25 11.4 11.4 0 0 0 3.6.57 1 1 0 0 1 1 1V20a1 1 0 0 1-1 1A17 17 0 0 1 3 4a1 1 0 0 1 1-1h3.5a1 1 0 0 1 1 1c0 1.25.2 2.45.57 3.57a1 1 0 0 1-.25 1z"/></svg>
        <span>832-361-9027</span>
      </div>
      <div class="contact-line">
        <svg viewBox="0 0 24 24" aria-hidden="true"><path d="M7 3h10v5H7zM4 9h16a2 2 0 0 1 2 2v6h-4v4H6v-4H2v-6a2 2 0 0 1 2-2zm4 7v3h8v-3z"/></svg>
        <span>832-614-7359</span>
      </div>
    </div>

    <div class="header-rule"></div>

    <svg class="corner-bands" viewBox="0 0 680 60" aria-hidden="true">
      <defs>
        <linearGradient id="redBand" x1="0" y1="0" x2="1" y2="0">
          <stop offset="0" stop-color="#d5141f"/>
          <stop offset="1" stop-color="#7a0410"/>
        </linearGradient>
      </defs>
      <polygon points="0,52 378,38 378,60 0,60" fill="var(--navy)"/>
      <polygon points="390,24 680,10 680,60 384,60" fill="url(#redBand)"/>
    </svg>
  </div>
</body>
</html>
```